New Innovative Counselling and psychotherapy Service needs Business Card design

Keep it simple and professional. On one side, just company name and logo (perhaps in all blue) and maybe a tag line.

On other side (all white) my name and Qualifications in centre

Industry/Entity Type

Health And Wellness

Contact Information for Business Card

Dara Whelby
Counsellor & Psychotherapist
BSc (Psychol.), BA, Dip. (Couns. & Psych.), PG.Cert (CBT), FGTrK, ONRE

I will also require Mobile no, Email and web site address of which I'll pass on to final designer.

Font styles to use
Sans Serif

Requirements
Must have
• My Logo Only and please use the colours in logo that is in it.
Should not have
• Any other images

```html
<!DOCTYPE html>
<html lang="en">
<head>
<meta charset="UTF-8">
<title>Kelden Row – Business Card</title>
<link rel="stylesheet" href="https://fonts.googleapis.com/css2?family=Roboto:wght@400;700&display=swap">
<style>
  :root {
    --backdrop: #3a3a3c;
    --card: #262628;
    --card-emboss: #3b3b3e;
    --blue: #3fa9e6;
    --green: #8cc63f;
    --ink: #ffffff;
    --ink-soft: #e6e6e6;
  }
  * { box-sizing: border-box; margin: 0; padding: 0; }
  html, body {
    width: 799px;
    height: 1200px;
    overflow: hidden;
    background: var(--backdrop);
    font-family: "Roboto", Arial, sans-serif;
  }
  .canvas {
    position: relative;
    width: 799px;
    height: 1200px;
  }
  .card {
    position: absolute;
    left: 80px;
    width: 640px;
    height: 370px;
    background: var(--card);
    border-radius: 28px;
    overflow: hidden;
  }
  .card--front { top: 115px; }
  .card--back { top: 715px; }

  /* Front */
  .front-lockup {
    position: absolute;
    inset: 0;
    display: flex;
    align-items: center;
    justify-content: center;
    gap: 16px;
  }
  .front-lockup__dot {
    width: 58px;
    height: 58px;
    border-radius: 50%;
    background: var(--card-emboss);
  }
  .front-lockup__name {
    font-size: 44px;
    font-weight: 400;
    color: var(--card-emboss);
    letter-spacing: 0.5px;
  }

  /* Back */
  .edge-bar {
    position: absolute;
    top: 34px;
    bottom: 34px;
    width: 14px;
    background: var(--blue);
  }
  .edge-bar--left { left: 0; border-radius: 0 12px 12px 0; }
  .edge-bar--right { right: 0; border-radius: 12px 0 0 12px; }

  .details {
    position: absolute;
    left: 48px;
    top: 60px;
    color: var(--ink);
  }
  .details__name {
    font-size: 24px;
    font-weight: 700;
    color: var(--blue);
    margin-bottom: 4px;
  }
  .details__role {
    font-size: 13px;
    line-height: 1.35;
    color: var(--ink-soft);
  }
  .contact {
    list-style: none;
    margin-top: 20px;
  }
  .contact__item {
    display: flex;
    align-items: center;
    gap: 14px;
    font-size: 16px;
    line-height: 1.6;
  }
  .contact__icon { width: 14px; height: 14px; flex: none; }

  .brand {
    position: absolute;
    right: 50px;
    bottom: 64px;
    display: flex;
    align-items: center;
    gap: 14px;
  }
  .brand__dot {
    width: 44px;
    height: 44px;
    border-radius: 50%;
    background: var(--blue);
  }
  .brand__name {
    font-size: 34px;
    font-weight: 400;
    color: var(--ink);
  }
</style>
</head>
<body>
<main class="canvas">

  <section class="card card--front" aria-label="Card front">
    <div class="front-lockup">
      <span class="front-lockup__dot"></span>
      <span class="front-lockup__name">Kelden Row</span>
    </div>
  </section>

  <section class="card card--back" aria-label="Card back">
    <span class="edge-bar edge-bar--left"></span>
    <span class="edge-bar edge-bar--right"></span>

    <div class="details">
      <h1 class="details__name">Dara Whelby</h1>
      <p class="details__role">Counsellor &amp; Psychotherapist</p>
      <p class="details__role">BSc (Psychol.), BA, Dip. (Couns. &amp; Psych.),</p>
      <p class="details__role">PG.Cert (CBT), FGTrK, ONRE</p>

      <ul class="contact">
        <li class="contact__item">
          <svg class="contact__icon" viewBox="0 0 14 14" aria-hidden="true">
            <path d="M2 1h3l1 3-2 1.5a8 8 0 0 0 4.5 4.5L10 8l3 1v3a1 1 0 0 1-1 1A11 11 0 0 1 1 2a1 1 0 0 1 1-1z" fill="var(--green)"/>
          </svg>
          0123 456 7890
        </li>
        <li class="contact__item">
          <svg class="contact__icon" viewBox="0 0 14 14" aria-hidden="true">
            <rect x="0.5" y="2.5" width="13" height="9" rx="1" fill="var(--green)"/>
            <path d="M1 3l6 5 6-5" stroke="var(--card)" stroke-width="1.2" fill="none"/>
          </svg>
          dara.w@KeldenRow.com
        </li>
        <li class="contact__item">
          <svg class="contact__icon" viewBox="0 0 14 14" aria-hidden="true">
            <circle cx="7" cy="7" r="6" fill="var(--blue)"/>
            <path d="M1 7h12M7 1c-3 3-3 9 0 12M7 1c3 3 3 9 0 12" stroke="var(--green)" stroke-width="1" fill="none"/>
          </svg>
          www.KeldenRow.com
        </li>
      </ul>
    </div>

    <div class="brand">
      <span class="brand__dot"></span>
      <span class="brand__name">Kelden Row</span>
    </div>
  </section>

</main>
</body>
</html>
```